New Fun, Positive, energised looking Business Card Needed for High Achiever Coach

I am looking for a two sided full colour business card. I am self employed and have recently re branded my 1-2-1 work re-vitalising high achievers. My target client base for these cards is therefore high achievers - usually aged 40 -55, they are often entrepreneurs, CEO or work in banking and finance and 2/3 are male. I work with them on 90 day or 6 month coaching programs to help them live their success in a healthier, more sustainable and fulfiiled way. They pay for this privately so though they are corporate types the cards need not look 'corporate'. I want to portray the idea of transformation, vitality and re-connecting.
You can get a feel for the look I like on my new website: morvenlisk.co.uk
I want to use this logo with strapline (Re-Vitalising High Achievers) (I purchased off Logoharbor) and font/ colours (the turquoise and green).
Details to include on the card:
www.morvenlisk.co.uk
+44 7915 302618
morven@morvenlisk.co.uk
skype: morvenlisk
I'd also like to include:
Do you struggle to switch off? Want to be healthier and feel fitter? Want closer relationships? More clarity over the direction you are headed? I can help you do these things using integrated mind-body techniques. Visit morvenlisk.co.uk TODAY to apply for a FREE Breakthrough session.
BUT if that is too much text for a card I am open to advice/ammendments.
Updates
Thanks for your design - I am considering them. PLease change the wording to :

```html
<!DOCTYPE html>
<html lang="en">
<head>
<meta charset="utf-8">
<title>Morven Lisk – Business Card</title>
<link rel="stylesheet" href="https://fonts.googleapis.com/css2?family=Open+Sans:ital,wght@0,400;0,700;1,400&display=swap">
<style>
  :root {
    --backdrop: #e9e6e1;
    --card: #0b0b0c;
    --turquoise: #1ba6d1;
    --green: #5bb85a;
    --white: #ffffff;
    --muted: #d6d6d6;
    --divider: #6d6d6d;
  }
  * { box-sizing: border-box; margin: 0; padding: 0; }
  html, body {
    width: 1200px; height: 720px; overflow: hidden;
    background: var(--backdrop);
    font-family: "Open Sans", Arial, sans-serif;
  }
  .stage {
    position: relative; width: 1200px; height: 720px;
    display: flex; align-items: center; justify-content: center; gap: 40px;
  }
  .card {
    position: relative; width: 540px; height: 320px;
    background: var(--card); overflow: hidden;
    box-shadow: 0 6px 18px rgba(0,0,0,.25);
  }

  /* Front */
  .card-front .swoosh { position: absolute; inset: 0; }
  .brand {
    position: absolute; left: 38px; top: 92px; width: 220px; text-align: center;
  }
  .brand-name {
    font-size: 30px; font-weight: 700; color: var(--turquoise); line-height: 1.1;
  }
  .brand-strapline {
    margin-top: 4px; font-size: 13px; font-style: italic; color: var(--turquoise);
  }
  .divider {
    position: absolute; left: 272px; top: 36px; width: 1px; height: 100px;
    background: linear-gradient(to bottom, transparent, var(--divider), transparent);
  }
  .contact {
    position: absolute; left: 290px; top: 40px; list-style: none;
    color: var(--white); font-size: 14px;
  }
  .contact li { display: flex; align-items: center; gap: 8px; height: 28px; }
  .contact svg { width: 14px; height: 14px; flex: none; }
  .website { font-weight: 700; letter-spacing: 1px; font-size: 15px; fill: var(--white); }

  /* Back */
  .card-back {
    display: flex; align-items: center; justify-content: center;
    text-align: center; color: var(--white);
  }
  .pitch { font-size: 16.5px; line-height: 1.32; }
  .pitch p + p { margin-top: 12px; }
  .pitch strong { font-weight: 700; }
</style>
</head>
<body>
<main class="stage">
  <section class="card card-front" aria-label="Business card front">
    <svg class="swoosh" viewBox="0 0 540 320" aria-hidden="true">
      <path d="M0 268 C180 282 330 198 540 146 L540 156 C330 208 180 292 0 278 Z" fill="var(--green)"/>
      <path d="M0 278 C180 292 330 208 540 156 L540 160 C330 212 180 296 0 282 Z" fill="var(--white)"/>
      <path d="M0 282 C180 296 330 212 540 160 L540 228 C360 256 180 312 0 302 Z" fill="var(--turquoise)"/>
      <text class="website" x="518" y="206" text-anchor="end" transform="rotate(-7 518 206)">www.morvenlisk.co.uk</text>
    </svg>

    <div class="brand">
      <div class="brand-name">Morven Lisk</div>
      <div class="brand-strapline">Re-Vitalising High Achievers</div>
    </div>

    <div class="divider"></div>

    <ul class="contact">
      <li>
        <svg viewBox="0 0 16 16" aria-hidden="true"><circle cx="8" cy="8" r="7.2" fill="none" stroke="var(--white)" stroke-width="1.2"/><path d="M5.2 4.3l1.4-.3.8 1.9-.9.7c.5 1.1 1.2 1.8 2.3 2.3l.7-.9 1.9.8-.3 1.4c-3 .2-6-2.8-5.9-5.9z" fill="var(--white)"/></svg>
        <span>+44 7915 302618</span>
      </li>
      <li>
        <svg viewBox="0 0 16 16" aria-hidden="true"><rect x="1.5" y="3.5" width="13" height="9" rx="1" fill="none" stroke="var(--white)" stroke-width="1.3"/><path d="M1.8 4l6.2 5 6.2-5" fill="none" stroke="var(--white)" stroke-width="1.3"/></svg>
        <span>morven@morvenlisk.co.uk</span>
      </li>
      <li>
        <svg viewBox="0 0 16 16" aria-hidden="true"><circle cx="8" cy="8" r="7" fill="var(--turquoise)"/></svg>
        <span>morvenlisk</span>
      </li>
    </ul>
  </section>

  <section class="card card-back" aria-label="Business card back">
    <div class="pitch">
      <p>Do you struggle to switch off?<br>
      Want to be healthier and feel fitter?<br>
      Want closer relationships?<br>
      More clarity over the direction you are headed?</p>
      <p>I can help you do these things using integrated<br>
      mind-body techniques.</p>
      <p>Visit <strong>morvenlisk.co.uk</strong> TODAY to apply for a<br>
      FREE Breakthrough session.</p>
    </div>
  </section>
</main>
</body>
</html>
```